indépendant en tant que Massothérapeute et Préparateur Mental, j'ai besoin de ...

Massothérapeute et préparateur mental indépendant, je recherche une carte de visite sobre et dynamique, sans images liées au massage ou à la préparation mentale mais intégrant mon logo. Les couleurs que j'aime bien sont : Blanc, gris, anthracite, noir et jaune

Contact Information for Business Card

carte de préférence Horizontale
neutre qui puisse toucher le deux domaines Massothérapie et préparation mentale

Requirements
Must have
• mon projet doit intégrer au recto:
LOGO
Loïc Bardèze
078 513 26 48
info@loicbardeze.ch
et éventuellement www.loicbardeze.ch

et au verso les deux adresses:

Chemin des Ormilles 7B
1400 Yverdon-les-Bains

Route de la Gravière 9
1725 Corbelin

Should not have
• mon projet ne doit pas contenir d'image en liens avec le massage ni la préparation mentale.

```html
<!DOCTYPE html>
<html lang="fr">
<head>
<meta charset="utf-8">
<title>Loïc Bardèze – Cartes de visite</title>
<link rel="stylesheet" href="https://fonts.googleapis.com/css2?family=Oswald:wght@500&family=Mulish:wght@600;700&display=swap">
<style>
  :root {
    --backdrop: #8e8e8e;
    --paper: #ffffff;
    --ink: #231f20;
    --ink-soft: #4a4647;
    --anthracite: #262223;
    --silver: #a59da1;
    --silver-dim: #6f686b;
    --band-text: #ffffff;
  }
  html, body {
    margin: 0;
    padding: 0;
    width: 1200px;
    height: 1200px;
    overflow: hidden;
    background: var(--backdrop);
  }
  .sheet {
    position: relative;
    width: 1200px;
    height: 1200px;
  }
  .card {
    position: absolute;
    left: 257px;
    width: 686px;
    height: 391px;
    border-radius: 26px;
    overflow: hidden;
  }
  .card--front { top: 166px; background: var(--paper); }
  .card--back  { top: 654px; background: var(--anthracite); }

  .front__name {
    position: absolute;
    right: calc(686px - 322px);
    top: 178px;
    margin: 0;
    font-family: "Oswald", sans-serif;
    font-weight: 500;
    font-size: 34px;
    line-height: 42px;
    letter-spacing: 0.3px;
    color: var(--ink);
    text-transform: uppercase;
    white-space: nowrap;
  }
  .front__divider {
    position: absolute;
    left: 346px;
    top: 147px;
    width: 1.5px;
    height: 98px;
    background: var(--ink);
  }
  .front__addresses {
    position: absolute;
    left: 369px;
    top: 145px;
    margin: 0;
    font-family: "Mulish", sans-serif;
    font-weight: 600;
    font-size: 14.5px;
    line-height: 19.5px;
    color: var(--ink-soft);
    font-style: normal;
  }
  .front__addresses .address + .address { margin-top: 3px; }
  .front__band {
    position: absolute;
    left: 0;
    top: 324px;
    width: 100%;
    height: 28px;
    background: var(--ink);
    display: flex;
    align-items: center;
    justify-content: center;
    font-family: "Mulish", sans-serif;
    font-weight: 700;
    font-size: 14px;
    letter-spacing: 0.4px;
    color: var(--band-text);
    white-space: nowrap;
  }
  .front__band .sep { margin: 0 4px; }

  .back__brand {
    position: absolute;
    left: 0;
    right: 0;
    top: 162px;
    display: flex;
    align-items: center;
    justify-content: center;
    gap: 18px;
  }
  .brand__mark {
    width: 46px;
    height: 46px;
    background: var(--silver);
  }
  .brand__text { display: flex; flex-direction: column; }
  .brand__name {
    font-family: "Mulish", sans-serif;
    font-weight: 700;
    font-size: 30px;
    line-height: 34px;
    color: var(--silver);
    letter-spacing: 1px;
  }
  .brand__trade {
    font-family: "Mulish", sans-serif;
    font-weight: 600;
    font-size: 10.5px;
    letter-spacing: 1.5px;
    color: var(--silver-dim);
    text-transform: uppercase;
  }
</style>
</head>
<body>
<main class="sheet">
  <section class="card card--front" aria-label="Recto">
    <h1 class="front__name">Loïc Bardèze</h1>
    <div class="front__divider"></div>
    <address class="front__addresses">
      <div class="address">Chemin des<br>Ormilles 7B<br>1415 Val-de-Moret</div>
      <div class="address">Route de la Gravière 9<br>1725 Corbelin</div>
    </address>
    <div class="front__band">
      <span>078 513 26 48</span><span class="sep">|</span><span>info@loicbardeze.ch</span><span class="sep">|</span><span>www.loicbardeze.ch</span>
    </div>
  </section>

  <section class="card card--back" aria-label="Verso">
    <div class="back__brand">
      <div class="brand__mark"></div>
      <div class="brand__text">
        <span class="brand__name">Loïc Bardèze</span>
        <span class="brand__trade">Massothérapeute / Préparateur Mental</span>
      </div>
    </div>
  </section>
</main>
</body>
</html>
```